Create modern and sleek business card for luxury real estate company

We're a "boutique" real estate office looking for a design that gets across a highly modern luxury brand. Blacks and whites are probably the best colors unless we try a silver foil for the logo. I've attached a version of our current logo here. I'd like to swap out the current font on there with Gotham Light Regular.

I'm looking to have one side of the card have the logo with the space for our agents info on the other side.

Target Market(s)

Young professionals in a "luxury" headspace

Industry/Entity Type

Real estate

Contact Information for Business Card

A place for agent name, cell number, website. The slogan "Quietly Redefining Fine Homes".

Font styles to use
Other font styles liked:
• Gotham Regular

Colors

Designer to choose only greyscale colors for use in the design.

Requirements
Must have
• Matte black as the background color. Clean lines and use of contrast. A specific design aspect that will use silver foil.
Nice to have
• Up in the air on integrating a QR code
Should not have
• Any houses or other real estate related design (ex: a clip art house)

```html
<!DOCTYPE html>
<html lang="en">
<head>
<meta charset="UTF-8">
<title>Halden Realty – Business Card</title>
<link href="https://fonts.googleapis.com/css2?family=Montserrat:wght@300;400;600&display=swap" rel="stylesheet">
<style>
  :root {
    --backdrop: #3a3a3c;
    --card: #0d0d0e;
    --silver: #e6e6e6;
    --muted: #8a8a8a;
    --rule: #5a5a5a;
    --emboss: #2a2a2c;
  }
  * { margin: 0; padding: 0; box-sizing: border-box; }
  html, body {
    width: 1200px; height: 801px; overflow: hidden;
    background: var(--backdrop);
    font-family: "Montserrat", sans-serif;
  }
  .stage {
    width: 1200px; height: 801px;
    display: flex; align-items: center; justify-content: center; gap: 40px;
  }
  .card {
    width: 520px; height: 297px;
    background: var(--card);
    position: relative; overflow: hidden;
    box-shadow: 0 14px 30px rgba(0,0,0,.45);
  }

  /* Info side */
  .card--info { display: flex; align-items: center; padding: 0 34px 30px; }
  .brand { display: flex; align-items: center; gap: 12px; }
  .brand__mark {
    width: 40px; height: 40px; border-radius: 50%;
    border: 2px solid var(--silver); flex: none;
  }
  .brand__name {
    color: var(--silver); font-weight: 400;
    font-size: 21px; line-height: 1.15; letter-spacing: 1.5px;
  }
  .divider { width: 1px; height: 96px; background: var(--rule); margin: 0 22px; flex: none; }
  .agent__name { color: #fff; font-weight: 600; font-size: 17px; letter-spacing: .5px; }
  .agent__title { color: var(--muted); font-weight: 300; font-size: 13px; margin: 2px 0 10px; }
  .contact { list-style: none; }
  .contact li {
    display: flex; align-items: center; gap: 8px;
    color: var(--silver); font-size: 12.5px; font-weight: 300; line-height: 1.7;
  }
  .contact svg { width: 11px; height: 11px; fill: var(--silver); flex: none; }
  .tagline {
    position: absolute; left: 0; right: 0; bottom: 32px; text-align: center;
    color: var(--silver); font-size: 13px; font-weight: 300; letter-spacing: .3px;
  }

  /* Logo side */
  .card--logo { display: flex; align-items: center; justify-content: flex-end; padding-right: 40px; }
  .backdrop-ring {
    position: absolute; left: -20px; top: 36px;
    width: 270px; height: 270px; border-radius: 50%;
    border: 7px solid var(--emboss);
  }
  .card--logo .brand__name { font-size: 32px; letter-spacing: 2px; position: relative; }
</style>
</head>
<body>
<main class="stage">
  <section class="card card--info">
    <div class="brand">
      <div class="brand__mark"></div>
      <div class="brand__name">HALDEN<br>REALTY</div>
    </div>
    <div class="divider"></div>
    <div class="agent">
      <h1 class="agent__name">DANIEL MOREAU</h1>
      <p class="agent__title">President</p>
      <ul class="contact">
        <li><svg viewBox="0 0 24 24"><path d="M6.6 10.8a15 15 0 0 0 6.6 6.6l2.2-2.2a1 1 0 0 1 1-.25 11.4 11.4 0 0 0 3.6.57 1 1 0 0 1 1 1V20a1 1 0 0 1-1 1A17 17 0 0 1 3 4a1 1 0 0 1 1-1h3.5a1 1 0 0 1 1 1c0 1.25.2 2.45.57 3.57a1 1 0 0 1-.25 1z"/></svg>555-014-2870</li>
        <li><svg viewBox="0 0 24 24"><path d="M2 5h20v14H2zm2 2v.5l8 5 8-5V7l-8 5z"/></svg>dmoreau@haldenrealty.com</li>
        <li><svg viewBox="0 0 24 24"><circle cx="12" cy="12" r="10"/></svg>www.haldenrealty.com</li>
      </ul>
    </div>
    <p class="tagline">Quietly Redefining Fine Homes</p>
  </section>

  <section class="card card--logo">
    <div class="backdrop-ring"></div>
    <div class="brand__name">HALDEN<br>REALTY</div>
  </section>
</main>
</body>
</html>
```